Small Business Broker Business Card Design

A business card design for a small business brokerage, which is a financial service, not unlike real estate brokerage, but for small businesses such as laundromats, pizza shops, restaurants, cleaners etc. The designs should all be simple, more conservative in nature, using the colors and font of the logo. Again, think real estate Brokerage as a business context
Contact Information for Business Card
Name: Glen R. Harlow. Title: Small Business Advisor. Email: g.harlow@bayfieldcapitalworks.example. Mobile: (555) 274-3918. Office: (555) 806-2147. www.bayfieldcapitalworks.example

```html
<!DOCTYPE html>
<html lang="en">
<head>
<meta charset="utf-8">
<title>Bayfield Capital Works – Business Card</title>
<link rel="stylesheet" href="https://fonts.googleapis.com/css2?family=Montserrat:wght@400;600;700&display=swap">
<style>
  :root {
    --navy: #1c3a6b;
    --green: #8cc63f;
    --white: #ffffff;
    --ink: #2a2a2a;
    --backdrop: #3a3a3a;
  }
  * { margin: 0; padding: 0; box-sizing: border-box; }
  html, body {
    width: 1200px; height: 1200px; overflow: hidden;
    background: var(--backdrop);
    font-family: "Montserrat", Arial, sans-serif;
  }
  .sheet {
    width: 1200px; height: 1200px;
    display: flex; flex-direction: column; align-items: center; justify-content: center;
    gap: 60px;
  }
  .card {
    width: 900px; height: 514px; position: relative;
    box-shadow: 0 10px 30px rgba(0,0,0,.45);
  }
  .card--front { background: var(--navy); display: flex; align-items: center; justify-content: center; }
  .card--back { background: var(--white); }

  .brand { display: flex; flex-direction: column; }
  .brand__row { display: flex; align-items: center; gap: 18px; }
  .brand__square { width: 34px; height: 34px; background: var(--green); flex: none; }
  .brand__name {
    font-weight: 700; text-transform: uppercase; letter-spacing: .5px; line-height: 1;
    white-space: nowrap;
  }
  .brand__tagline {
    font-weight: 600; text-transform: uppercase; color: var(--green);
    letter-spacing: 2.2px; line-height: 1; margin-top: 10px; white-space: nowrap;
  }

  .card--front .brand__name { color: var(--white); font-size: 40px; }
  .card--front .brand__tagline { font-size: 17px; padding-left: 52px; }

  .contact {
    position: absolute; left: 390px; top: 70px;
    border-left: 2px solid var(--navy); padding-left: 24px;
  }
  .contact__name {
    font-weight: 700; font-size: 36px; color: var(--navy); text-transform: uppercase; line-height: 1;
  }
  .contact__title { font-size: 18px; color: var(--ink); margin-top: 6px; }
  .contact__list { list-style: none; margin-top: 22px; }
  .contact__item { font-size: 17px; color: var(--ink); line-height: 1.75; white-space: nowrap; }
  .contact__label { font-weight: 700; color: var(--navy); display: inline-block; width: 30px; }

  .card--back .brand { position: absolute; left: 60px; bottom: 58px; }
  .card--back .brand__square { background: var(--navy); }
  .card--back .brand__name { color: var(--navy); font-size: 40px; }
  .card--back .brand__tagline { font-size: 17px; padding-left: 52px; }
</style>
</head>
<body>
<main class="sheet">
  <section class="card card--front" aria-label="Card front">
    <div class="brand">
      <div class="brand__row">
        <span class="brand__square"></span>
        <span class="brand__name">Bayfield Capital Works, Inc</span>
      </div>
      <span class="brand__tagline">Clear guidance to buy or sell your business well</span>
    </div>
  </section>

  <section class="card card--back" aria-label="Card back">
    <div class="contact">
      <h1 class="contact__name">Glen R. Harlow</h1>
      <p class="contact__title">Small Business Advisor</p>
      <ul class="contact__list">
        <li class="contact__item"><span class="contact__label">M:</span>(555) 274-3918</li>
        <li class="contact__item"><span class="contact__label">O:</span>(555) 806-2147</li>
        <li class="contact__item"><span class="contact__label">E:</span>g.harlow@bayfieldcapitalworks.example</li>
        <li class="contact__item"><span class="contact__label">W:</span>www.bayfieldcapitalworks.example</li>
      </ul>
    </div>
    <div class="brand">
      <div class="brand__row">
        <span class="brand__square"></span>
        <span class="brand__name">Bayfield Capital Works, Inc</span>
      </div>
      <span class="brand__tagline">Clear guidance to buy or sell your business well</span>
    </div>
  </section>
</main>
</body>
</html>
```